Building Design company needing a letterhead

We need a letter head for our Building Design company to send letters etc. to our clients, consultants, councils etc. We would like to see our logo used and company colours. I have attached our style guide and an example of our current letterheads. Top left we would like our logo, top right we would like the company details and at the footer we would like some sort of image/design etc. that suits our brand. I like the Tarrow Design letterhead attached.

Target Market(s)

Professionals, Councils, Consultants, Mums & Dads

Industry/Entity Type

Architecture

Other font styles liked:
• refer the design style guide

Colors
f37122
000000
1b1b1b

Requirements
Must have
• Must have the minimum of a logo, company details and footer
Nice to have
• An image/design made for the footer that would suite our brand and website at www.corvanplans.com.au. Also it would be nice to include the KMEOT logo somewhere perhaps included in the footer.
Should not have
• Large images in the header. I just want the logo and company details.

```html
<!DOCTYPE html>
<html lang="en">
<head>
<meta charset="utf-8">
<title>Corvan Plans Letterhead</title>
<link href="https://fonts.googleapis.com/css2?family=Arimo:wght@400&family=Open+Sans:wght@400;700&display=swap" rel="stylesheet">
<style>
  :root {
    --orange: #f37122;
    --black: #000000;
    --ink: #1b1b1b;
    --paper: #f7f7f6;
    --backdrop: #e4e2de;
  }
  * { margin: 0; padding: 0; box-sizing: border-box; }
  html, body {
    width: 1189px; height: 1200px; overflow: hidden;
    background: var(--backdrop);
  }
  .letterhead {
    position: absolute; left: 138px; top: 9px;
    width: 912px; height: 1182px;
    background: var(--paper);
    color: var(--ink);
  }
  .brand {
    position: absolute; left: 75px; top: 78px;
    display: flex; align-items: center; gap: 22px;
  }
  .brand-square { width: 58px; height: 58px; background: var(--orange); }
  .brand-name {
    font-family: "Open Sans", sans-serif; font-weight: 700;
    font-size: 46px; line-height: 48px; letter-spacing: 3px;
    color: var(--ink);
  }
  .letter-body {
    position: absolute; left: 75px; top: 276px; width: 768px;
    font-family: Arimo, Arial, sans-serif; font-size: 17px; line-height: 27px;
    color: var(--ink);
  }
  .letter-body p { margin-bottom: 27px; }
  .letter-body p.spaced { margin-top: 54px; }
  .footer-rule {
    position: absolute; left: 78px; top: 1070px;
    width: 693px; height: 5px; background: var(--black);
  }
  .contact {
    position: absolute; top: 1090px;
    font-family: "Open Sans", sans-serif; font-size: 14px; line-height: 21px;
    color: var(--ink);
  }
  .contact-phone { left: 78px; }
  .contact-web { left: 251px; }
  .contact-address { left: 499px; }
  .contact .label { color: var(--orange); }
  .contact-row { display: flex; align-items: center; gap: 8px; }
  .contact-row svg { flex: none; }
  .divider {
    position: absolute; top: 1092px; width: 3px; height: 36px; background: var(--black);
  }
  .divider-one { left: 228px; }
  .divider-two { left: 481px; }
  .member-badge {
    position: absolute; left: 784px; top: 1055px;
    display: flex; flex-direction: column; align-items: center; gap: 6px;
  }
  .member-badge .badge-square {
    width: 66px; height: 70px; border: 3px solid var(--orange);
  }
  .member-badge .badge-name {
    font-family: "Open Sans", sans-serif; font-size: 16px; color: var(--orange);
    letter-spacing: 1px;
  }
</style>
</head>
<body>
<main class="letterhead">
  <header class="brand">
    <div class="brand-square"></div>
    <div class="brand-name">CORVAN<br>PLANS</div>
  </header>

  <section class="letter-body">
    <p>Lorem Ipsum is simply dummy text of the printing and typesetting industry. Lorem Ipsum has been the industry’s standard dummy text ever since the 1500s, when an unknown printer took a galley of type and scrambled it to make a type specimen book. It has survived not only five centuries, but also the leap into electronic typesetting, remaining essentially unchanged. It was popularised in the 1960s with the release of Transferline sheets containing Lorem Ipsum passages, and more recently with desktop publishing software like Folio PageSetter including versions of Lorem Ipsum.</p>
    <p>It is a long established fact that a reader will be distracted by the readable content of a page when looking at its layout. The point of using Lorem Ipsum is that it has a more-or-less normal distribution of letters, as opposed to using ’Content here, content here’, making it look like readable English. Many desktop publishing packages and web page editors now use Lorem Ipsum as their default model text, and a search for ’lorem ipsum’ will uncover many web sites still in their infancy. Various versions have evolved over the years, sometimes by accident, sometimes on purpose (injected humour and the like).</p>
    <p class="spaced">Contrary to popular belief, Lorem Ipsum is not simply random text. It has roots in a piece of classical Latin literature from 45 BC, making it over 2000 years old. Daniel Ashworth, a Latin professor at Alder Ridge College in Vermont, looked up one of the more obscure Latin words, consectetur, from a Lorem Ipsum passage, and going through the cites of the word in classical literature, discovered the undoubtable source. Lorem Ipsum comes from sections 1.10.32 and 1.10.33 of "de Finibus Bonorum et Malorum" structures, to generate Lorem Ipsum which looks reasonable. The generated Lorem Ipsum is therefore always free from repetition, injected humour, or non-characteristic words etc.</p>
  </section>

  <div class="footer-rule"></div>

  <div class="contact contact-phone">
    <div class="contact-row">
      <svg width="13" height="13" viewBox="0 0 13 13"><rect width="13" height="13" fill="var(--orange)"/><path d="M4 2.5 L5.5 4.5 L4.8 5.6 Q6 7.6 7.6 8.3 L8.6 7.5 L10.5 9 L9.6 10.6 Q5 10 2.6 4 Z" fill="#fff"/></svg>
      <span>(08) 6100 4821</span>
    </div>
    <div><span class="label">ABN</span> 41 308 226 914</div>
  </div>
  <div class="divider divider-one"></div>

  <div class="contact contact-web">
    <div class="contact-row">
      <svg width="13" height="13" viewBox="0 0 13 13"><rect width="13" height="13" fill="var(--orange)"/><rect x="3" y="4" width="7" height="5" fill="none" stroke="#fff" stroke-width="1"/><path d="M3 4 L6.5 7 L10 4" fill="none" stroke="#fff" stroke-width="1"/></svg>
      <span>admin@corvanplans.com.au</span>
    </div>
    <div class="contact-row">
      <svg width="13" height="13" viewBox="0 0 13 13"><rect width="13" height="13" fill="var(--orange)"/><circle cx="6.5" cy="6.5" r="3.5" fill="none" stroke="#fff" stroke-width="1"/><path d="M3 6.5 H10 M6.5 3 V10" stroke="#fff" stroke-width="1"/></svg>
      <span>www.corvanplans.com.au</span>
    </div>
  </div>
  <div class="divider divider-two"></div>

  <div class="contact contact-address">
    <div>Unit 3/22 Ardena Way Halcott WA 6190</div>
    <div>PO Box 5180 Halcott North WA 6190</div>
  </div>

  <div class="member-badge">
    <div class="badge-square"></div>
    <div class="badge-name">KMEOT</div>
  </div>
</main>
</body>
</html>
```